Tech business card design

We need an amazing business card design for our new business 'Pexla' a marketing tech startup based in Sydney, Australia. We provide an online marketplace for businesses to search and buy advertising media, connect with service providers and learn more about marketing. We wish to communicate 'cool tech', reliability and professionalism and design based around our logo.

Target Market(s)

Business Owners

Contact Information for Business Card

Name
Position
Email Address
Website
Phone Number

Font styles to use
Other font styles liked:
• Avenir & Avenir Next

Colors

Designer to choose colors to be used in the design.

```html
<!DOCTYPE html>
<html lang="en">
<head>
<meta charset="utf-8">
<title>Pexla business card</title>
<link rel="stylesheet" href="https://fonts.googleapis.com/css2?family=Nunito+Sans:wght@400;600;800&display=swap">
<style>
  :root{
    --navy:#1b1d63;
    --navy-deep:#12134a;
    --navy-light:#2a2d7c;
    --paper:#ffffff;
    --paper-shade:#eceef2;
    --stage:#e6e7ea;
    --ink:#1b1d63;
  }
  *{margin:0;padding:0;box-sizing:border-box}
  html,body{width:1200px;height:780px;overflow:hidden}
  body{background:var(--stage);font-family:"Nunito Sans",Arial,sans-serif;position:relative}
  .card{position:absolute;top:235px;width:540px;height:310px;border-radius:18px;overflow:hidden;
        box-shadow:0 6px 18px rgba(0,0,0,.18)}
  .card--front{left:40px;background:linear-gradient(135deg,var(--paper) 40%,var(--paper-shade))}
  .card--back{left:620px;background:radial-gradient(circle at 55% 45%,var(--navy-light),var(--navy-deep) 80%)}
  .swoosh{position:absolute;inset:0;width:100%;height:100%}
  .brand{font-weight:800;letter-spacing:-1px;line-height:1}
  .card--front .brand{position:absolute;top:46px;right:120px;font-size:84px;color:var(--ink)}
  .holder{position:absolute;left:34px;top:150px;color:var(--ink)}
  .holder__name{font-size:19px;font-weight:800}
  .holder__role{font-size:13px;font-weight:400;margin-top:1px}
  .contact{position:absolute;left:34px;top:205px;color:var(--ink);font-size:12.5px;line-height:1.35}
  .contact__address{margin-bottom:10px}
  .contact__row{display:flex;align-items:center;gap:6px}
  .contact__icon{width:13px;height:13px;flex:none}
  .web{font-size:12px;letter-spacing:3px;font-weight:600;color:#fff}
  .card--front .web{position:absolute;right:22px;bottom:22px}
  .card--back .brand{position:absolute;left:0;right:0;top:104px;text-align:center;font-size:96px;color:#fff}
  .card--back .web{position:absolute;left:0;right:0;top:218px;text-align:center;letter-spacing:5px}
</style>
</head>
<body>
  <section class="card card--front">
    <svg class="swoosh" viewBox="0 0 540 310" preserveAspectRatio="none" aria-hidden="true">
      <path d="M220 310 C360 300 400 70 540 20 L540 310 Z" fill="var(--navy)"/>
      <path d="M262 310 C390 296 430 96 540 52 L540 66 C440 110 404 298 292 310 Z" fill="#fff"/>
    </svg>
    <div class="brand">Pexla</div>
    <div class="holder">
      <div class="holder__name">Liam Carter</div>
      <div class="holder__role">Manager</div>
    </div>
    <div class="contact">
      <div class="contact__address">PO BOX 482, Harbour Lane<br>7th street Sydney<br>Australia</div>
      <div class="contact__row">
        <svg class="contact__icon" viewBox="0 0 16 16" aria-hidden="true"><circle cx="8" cy="8" r="8" fill="var(--ink)"/><path d="M5 4.5l1.6-.4.9 2-1 .8a5 5 0 0 0 2.6 2.6l.8-1 2 .9-.4 1.6c-3.6.3-6.8-2.9-6.5-6.5z" fill="#fff"/></svg>
        <span>555.204.7781</span>
      </div>
      <div class="contact__row">
        <svg class="contact__icon" viewBox="0 0 16 16" aria-hidden="true"><circle cx="8" cy="8" r="8" fill="var(--ink)"/><rect x="4" y="5" width="8" height="6" rx="1" fill="#fff"/><path d="M4.3 5.4 8 8.3l3.7-2.9" stroke="var(--ink)" stroke-width="1" fill="none"/></svg>
        <span>info@pexlamail.com</span>
      </div>
    </div>
    <div class="web">www.pexlaweb.com</div>
  </section>

  <section class="card card--back">
    <div class="brand">Pexla</div>
    <div class="web">www.pexlaweb.com</div>
  </section>
</body>
</html>
```